Colin Vardek Business card

Hey there, I’m hoping to have a business card designed. I’m in Real estate and just switched to a new Brokerage called: The Harbourline Property Group

The back could just be the company name maybe or whatever looks good!

I’ve attached some logos of our company and some cards my buddy had done up.

On the card:
Colin Vardek
colinvardek@mailora.com
587-412-9065
colinvardek.ca

Target Market(s)

Home buyers and sellers

Industry/Entity Type

Real Estate

Contact Information for Business Card

just looking for a cool and modern design with my picture on it. I like the idea of Black and red being used.

Requirements
Must have
• all the details provided. I'm open to anything. Just want a professional looking card.

```html
<!DOCTYPE html>
<html lang="en">
<head>
<meta charset="utf-8">
<title>Colin Vardek Business Card</title>
<link href="https://fonts.googleapis.com/css2?family=Montserrat:wght@800&family=Roboto:wght@400;500&display=swap" rel="stylesheet">
<style>
  :root {
    --red: #d21f3a;
    --red-deep: #a8142b;
    --red-bright: #ee1c3e;
    --ink: #1c1c1e;
    --paper: #ffffff;
    --stage: #2a2a2c;
    --photo-dark: #2b2f36;
    --photo-light: #c9b8ad;
  }
  * { box-sizing: border-box; margin: 0; padding: 0; }
  html, body { width: 1200px; height: 852px; overflow: hidden; }
  body { background: var(--stage); position: relative; font-family: "Roboto", Arial, sans-serif; }

  .card {
    position: absolute;
    width: 520px;
    height: 300px;
    border-radius: 22px;
    overflow: hidden;
  }

  /* Back */
  .card--back {
    left: 70px; top: 110px;
    background: linear-gradient(120deg, var(--red) 0%, var(--red) 55%, var(--red-bright) 100%);
  }
  .card--back .brand {
    position: absolute;
    left: 50px; top: 118px;
    width: 300px;
    color: var(--paper);
    font-family: "Montserrat", Arial, sans-serif;
    font-weight: 800;
    font-size: 30px;
    line-height: 1.05;
    text-transform: uppercase;
  }

  /* Front */
  .card--front {
    left: 610px; top: 440px;
    background: var(--paper);
    border-bottom: 4px solid var(--red);
  }
  .photo-band {
    position: absolute; left: 0; top: 0;
    width: 170px; height: 100%;
    background: var(--red);
  }
  .portrait {
    position: absolute; left: 40px; top: 84px;
    width: 220px; height: 216px;
    border-radius: 110px 110px 0 0;
    background: linear-gradient(180deg, var(--photo-light) 0%, var(--photo-dark) 55%, var(--photo-dark) 100%);
  }
  .accent-bar {
    position: absolute; right: 0; top: 46px;
    width: 14px; height: 40px;
    background: var(--red);
  }
  .card--front .brand {
    position: absolute;
    right: 40px; top: 22px;
    width: 250px;
    text-align: right;
    color: var(--ink);
    font-family: "Montserrat", Arial, sans-serif;
    font-weight: 800;
    font-size: 22px;
    line-height: 1.05;
    text-transform: uppercase;
  }
  .agent-name {
    position: absolute;
    right: 40px; top: 112px;
    color: var(--red);
    font-weight: 500;
    font-size: 20px;
  }
  .contact-list {
    position: absolute;
    right: 28px; top: 150px;
    list-style: none;
    text-align: right;
    color: var(--ink);
    font-size: 14px;
    line-height: 22px;
  }
  .contact-list li { display: flex; justify-content: flex-end; align-items: center; gap: 8px; }
  .contact-icon { width: 14px; height: 14px; flex: none; }
</style>
</head>
<body>
  <section class="card card--back" aria-label="Card back">
    <p class="brand">The Harbourline Property Group</p>
  </section>

  <section class="card card--front" aria-label="Card front">
    <div class="photo-band"></div>
    <div class="portrait" role="img" aria-label="Portrait photo of Colin Vardek in a dark suit and white shirt"></div>
    <div class="accent-bar"></div>
    <p class="brand">The Harbourline Property Group</p>
    <p class="agent-name">Colin Vardek</p>
    <ul class="contact-list">
      <li>587-412-9065
        <svg class="contact-icon" viewBox="0 0 14 14" aria-hidden="true"><circle cx="7" cy="7" r="7" fill="#d21f3a"/><path d="M4.5 3.5l1.5 0 .6 1.8-.9.7a5 5 0 0 0 2.3 2.3l.7-.9 1.8.6 0 1.5c-3.5.3-6.3-2.5-6-6z" fill="#fff"/></svg>
      </li>
      <li>colinvardek@mailora.com
        <svg class="contact-icon" viewBox="0 0 14 14" aria-hidden="true"><circle cx="7" cy="7" r="7" fill="#d21f3a"/><rect x="3.5" y="4.5" width="7" height="5" fill="none" stroke="#fff" stroke-width="1"/><path d="M3.5 4.5l3.5 3 3.5-3" fill="none" stroke="#fff" stroke-width="1"/></svg>
      </li>
      <li>colinvardek.ca
        <svg class="contact-icon" viewBox="0 0 14 14" aria-hidden="true"><circle cx="7" cy="7" r="7" fill="#d21f3a"/><circle cx="7" cy="7" r="3.6" fill="none" stroke="#fff" stroke-width="1"/><path d="M3.4 7h7.2M7 3.4c-1.6 2.2-1.6 5 0 7.2M7 3.4c1.6 2.2 1.6 5 0 7.2" fill="none" stroke="#fff" stroke-width=".8"/></svg>
      </li>
    </ul>
  </section>
</body>
</html>
```